Velmisa Sunscreen and Tanning Lotion Flyer

I need a flyer to post to pm Chatterloop and other social media.
It most have these components:
Modern, sensational fonts, Original Art work, Sexy, Theme based on Verses
Women, bikini, tan, attractive
Ocean scenes, Palm Trees (same green as bottle)
VELMISA Logo (Slight shading background)
Quote “Quality by Design”
Bright, Sunny, fun
Save in PDF, GIF, and EPS

Reason: I have some designer who have not completed their work. Thank you.

Target Market(s)

Sunscreen tanning lotion

Industry/Entity Type

Media

Colors
9bcb3c

Requirements
Must have
• Modern, sensational fonts, Original Art work, Sexy, Theme based on Verses
• Women, bikini, tan, attractive
• Ocean scenes, Palm Trees (same green as bottle)
• VELMISA Logo (Slight shading in the background)
• Quote “Quality by Design”
• Bright, Sunny, fun
• Save in PDF, GIF, and EPS
Nice to have
• flyer designed with these verses in mind.
• •When the warm sea breeze exhales its sweet serenity, and the frothy sea cloaks your body in indulgence, the rays of the sun completes the objective.
• • The water splatters against the shore, and the blue stillness showers me tranquility and perfection and I find myself covered by the seas delightful symphony.
• •The sea breeze feels like a long lost friend, as it delightfully caresses your sweaty skin. And like that long lost friend, you embrace, take a deep breath, and relish the gusto of life.
• • The stunningly-turquoise sea beckons and we enthusiastically surrender to its allure. A smile from the white puffy clouds above. A soothing massage from the wet, cool sand below our feet, bliss in the sun.
• •Seagulls have white plumage, not unlike the color to the clouds overhead. Their hue is undistinguishable from the whitecaps spawned by waves on a blustery day. Mother Nature must be an artist whose philosophy is harmony in symmetry
• It would be nice to have these verses incorporated in the Flyer, but it is not necessary.
Should not have
• Must not have someone else's work, all graphic need to be original.

```html
<!DOCTYPE html>
<html lang="en">
<head>
<meta charset="utf-8">
<title>Velmisa Sunscreen &amp; Suntan Lotion Flyer</title>
<link href="https://fonts.googleapis.com/css2?family=Cinzel:wght@600&family=Open+Sans:wght@600;700&family=Crimson+Text:ital@0;1&family=Great+Vibes&family=Bebas+Neue&family=Ubuntu:wght@700&display=swap" rel="stylesheet">
<style>
  :root {
    --panel-dark: #050b0c;
    --panel-teal: #0e3a3f;
    --gold: #e2b85a;
    --gold-soft: #f0c46a;
    --cream: #f4ecd6;
    --sea: #2bb5c8;
    --sand: #efe6d4;
    --palm: #9bcb3c;
    --sun-yellow: #ffd800;
    --navy: #1c2870;
    --copper: #c7782a;
    --ocean-band: #1a8ec6;
    --white: #ffffff;
  }
  * { margin: 0; padding: 0; box-sizing: border-box; }
  html, body { width: 1200px; height: 822px; overflow: hidden; background: #ffffff; }
  .flyer {
    position: relative; width: 1200px; height: 822px; overflow: hidden;
    background: linear-gradient(120deg, var(--panel-dark) 0%, #061416 35%, var(--panel-teal) 60%, #0c4b52 100%);
    font-family: "Open Sans", sans-serif;
  }
  .artwork { position: absolute; inset: 0; }
  .brand-mark {
    position: absolute; left: 118px; top: 36px; width: 148px; height: 148px; border-radius: 50%;
    background: radial-gradient(circle at 40% 35%, #f6d98a, #b9862e 70%, #7a531a);
  }
  .brand-name {
    position: absolute; left: 26px; top: 196px; white-space: nowrap;
    font-family: "Cinzel", serif; font-weight: 600; font-size: 62px; line-height: 1;
    color: var(--gold);
  }
  .brand-name sup { font-size: 20px; vertical-align: 34px; margin-left: 2px; }
  .brand-tagline {
    position: absolute; left: 29px; top: 274px; white-space: nowrap;
    font-weight: 600; font-size: 20px; color: var(--gold-soft);
  }
  .product-copy {
    position: absolute; left: 29px; top: 334px; width: 296px;
    font-family: "Crimson Text", serif; font-size: 13.4px; line-height: 18.4px;
    color: var(--cream); text-align: justify;
  }
  .origin {
    position: absolute; left: 29px; top: 690px; width: 344px; white-space: nowrap;
    font-weight: 600; font-size: 19px; line-height: 24px; color: var(--gold-soft);
    border-bottom: 1px solid var(--gold); padding-bottom: 3px;
  }
  .contact-note {
    position: absolute; left: 29px; top: 726px; white-space: nowrap;
    font-family: "Crimson Text", serif; font-style: italic; font-size: 18px; line-height: 22px; color: var(--white);
  }
  .contact-email {
    position: absolute; left: 29px; top: 757px; white-space: nowrap;
    font-family: "Ubuntu", sans-serif; font-weight: 700; font-size: 27px; line-height: 32px; letter-spacing: 1.5px;
    color: var(--gold-soft);
  }
  .claim-bubble {
    position: absolute; left: 405px; top: 72px; width: 220px; height: 160px;
    transform: rotate(-8deg);
    background: var(--sun-yellow); border-radius: 50% 46% 52% 48%;
    box-shadow: 0 0 0 3px #fff36a, 0 0 0 5px #e6b900;
    display: flex; align-items: center; justify-content: center; text-align: center;
    font-weight: 700; font-size: 24px; line-height: 27px; color: #2a1a05;
  }
  .launch-word {
    position: absolute; right: 12px; top: 334px;
    font-family: "Bebas Neue", sans-serif; font-size: 108px; line-height: 1; letter-spacing: 18px;
    color: var(--white); opacity: 0.92;
  }
  .texture-line {
    position: absolute; right: 28px; white-space: nowrap;
    font-family: "Great Vibes", cursive; color: var(--navy); font-size: 44px; line-height: 1;
  }
  .texture-line.first { top: 428px; }
  .texture-line.second { top: 470px; }
  .spf-badge {
    position: absolute; left: 969px; top: 518px; width: 194px; height: 194px; border-radius: 50%;
    background: radial-gradient(circle at 45% 35%, #e9a35a, var(--copper) 60%, #8d4c14);
    color: var(--white); text-align: center;
  }
  .spf-value { position: absolute; top: 40px; width: 100%; font-family: "Ubuntu", sans-serif; font-weight: 700; font-size: 56px; line-height: 1; }
  .spf-value span { font-size: 30px; }
  .spf-volume { position: absolute; top: 110px; width: 100%; font-weight: 700; font-size: 19px; }
  .signoff { position: absolute; right: 37px; top: 722px; text-align: right; color: var(--white); white-space: nowrap; }
  .signoff-brand { font-weight: 600; font-size: 17px; line-height: 22px; }
  .signoff-line { font-weight: 600; font-size: 19px; line-height: 24px; }
  .signoff-quote { font-weight: 700; font-size: 15px; line-height: 30px; }
</style>
</head>
<body>
<main class="flyer">
  <svg class="artwork" width="1200" height="822" viewBox="0 0 1200 822">
    <defs>
      <clipPath id="scene-window">
        <circle cx="752" cy="424" r="378"/>
        <rect x="860" y="0" width="340" height="822"/>
      </clipPath>
      <linearGradient id="beach-tones" x1="0" y1="0" x2="0" y2="1">
        <stop offset="0" stop-color="#3f9ee0"/>
        <stop offset="0.45" stop-color="#a9d8f2"/>
        <stop offset="0.62" stop-color="var(--sea)"/>
        <stop offset="0.78" stop-color="#7fd3dc"/>
        <stop offset="1" stop-color="var(--sand)"/>
      </linearGradient>
      <linearGradient id="frond-tones" x1="0" y1="0" x2="0" y2="1">
        <stop offset="0" stop-color="var(--palm)" stop-opacity="0.8"/>
        <stop offset="1" stop-color="var(--palm)" stop-opacity="0"/>
      </linearGradient>
    </defs>
    <g role="img" aria-label="Photo of a tanned woman in a white bikini on a tropical beach with palm trees and turquoise sea">
      <rect x="0" y="0" width="1200" height="822" fill="url(#beach-tones)" clip-path="url(#scene-window)"/>
    </g>
    <g role="img" aria-label="Green palm fronds hanging across the top edge">
      <rect x="330" y="0" width="870" height="150" fill="url(#frond-tones)" opacity="0.7"/>
    </g>
    <circle cx="752" cy="424" r="378" fill="none" stroke="#0d4e57" stroke-width="5"/>
    <circle cx="758" cy="420" r="386" fill="none" stroke="#ffffff" stroke-width="1.5" opacity="0.8"/>
    <path d="M900 822 C980 740 1080 706 1200 664 L1200 822 Z" fill="var(--ocean-band)"/>
    <path d="M890 790 C975 712 1080 680 1200 650" fill="none" stroke="#ffffff" stroke-width="2" opacity="0.8"/>
  </svg>

  <div class="brand-mark"></div>
  <div class="brand-name">VELMISA<sup>™</sup></div>
  <div class="brand-tagline">SUNSCREEN &amp; SUNTAN LOTION</div>

  <p class="product-copy">Velmisa Tanning Lotion is the most extra ordinary and innovative sun tanning product to emerge in several generations. The constituents of this product are formidable substances that protect the skin against the aftermath of sun exposure-before you exposed yourself to the sun's rays. The Aloe Vera in this product along with other oils and cream are specifically manufactured to lessen the symptoms of extended exposure to the sun. Velmisa is designed to provide a broad spectrum protection (50) that assist in the reduction of (UVA) and (UVB) radiation to create a magnificent sun absorbing and long lasting deep dark bronzing experience. It is an elegant gift from nature that leaves your skin feeling fresh and not greasy. It is water resistant contains no preservatives or coloring agents. Velmisa Tanning Lotion is manufactured utilizing the finest raw materials.</p>

  <div class="origin">Product of the USA: Port Calder, NY</div>
  <div class="contact-note">For comments or suggestions please contact us at</div>
  <div class="contact-email">hello@velmisasun.com</div>

  <div class="claim-bubble">Reduction<br>to (UVA)<br>and (UVB)<br>Radiation</div>

  <div class="launch-word">NEW</div>
  <div class="texture-line first">Sophisticated</div>
  <div class="texture-line second">Velvety &amp; Smooth</div>

  <div class="spf-badge">
    <div class="spf-value">50<span>SPF</span></div>
    <div class="spf-volume">8FL OZ| 237ml</div>
  </div>

  <div class="signoff">
    <div class="signoff-brand">VELMISA™</div>
    <div class="signoff-line">Tanning Lotion &amp; Sunscreen</div>
    <div class="signoff-quote">Quality by Design</div>
  </div>
</main>
</body>
</html>
```